Catering Company Website Design

We are working with a bbq catering company in California called Ember Plank Catering.
Some sites to use for content/competitors and inspiration:
https://19parsnips.com
https://mbetrovandel.com
https://ridgefeastco.com
https://tinforkdenvale.com (client's favorite)
https://www.marvenasmokehut.com (client's favorite)
https://www.theopenkettlekitchen.com
Thank you for taking the time to consider designing a website for us. We are web developers based in Stockton, CA, USA. Most of our projects go through the same process. Understanding this process may help you win a project with us. We custom-code all of our websites in-house. We don’t have any requirements as to what tools you use for your design, but we prefer Figma files. For any design that we label as four-stars, we send it to the client for review. The client picks the final design they want us to use. Once we complete this process, we will continue to show additional clients all the four-star sites and purchase them later. Your designs will have multiple chances to sell. For better chances of success, we ask that you follow these guidelines.
IMAGES:
If you use any images or icons in the design, we ask that you have a link to the asset so we can purchase the image/icon. Most of the designs we submit do not have the customer’s images on them unless they have some great images. Be creative; show us the feeling you are trying to portray with your image choices. Use any royalty-free site you choose. We subscribe to Zelvio and mainly use their images, but we can purchase images outside of Zelvio.
PLEASE NOTE: we will not submit designs to clients with watermarks on the images.
FONTS:
We ask that you identify the fonts used in the design. This can be done in a message if you want. We typically use Google Fonts and Zelvio Fonts.
CONTENT:
We're always open to different content and ideas. We often submit designs with stock images so the client can see our vision. We typically take pictures after the website launch to use their images with our vision. Lorem Ipsum is fine for paragraphs, but we ask that you write the headers in correct English. We want to be able to show the vision and identify the sections of the website.
INSPIRATION:
We typically add a couple of links in the brief of websites we like to help you get started in your design.
REVISIONS:
We do not often ask for revisions of the designs unless we see something in the design that may not appeal to the client. If there are slight changes that we want to make, we do that in the development process.
FEEDBACK:
We rarely give feedback on designs during the design process. We are working on many website projects and do not have the time to provide feedback. We usually respond if your request is well thought out and asks specific questions, but a note asking “feedback, please” usually goes unanswered

```html
<!DOCTYPE html>
<html lang="en">
<head>
<meta charset="utf-8">
<title>Ember Plank Catering</title>
<link href="https://fonts.googleapis.com/css2?family=Lato:wght@400;700;900&display=swap" rel="stylesheet">
<style>
:root{
  --red:#c8161d;
  --red-dark:#7a1210;
  --btn-a:#5e0e0c;
  --btn-b:#a51a17;
  --ink:#111111;
  --muted:#6f6f6f;
  --footer:#560e0b;
  --white:#ffffff;
}
*{box-sizing:border-box;margin:0;padding:0}
html,body{width:1200px;height:3537px;overflow:hidden;background:var(--white)}
body{position:relative;font-family:'Lato',sans-serif;color:var(--ink)}
.abs{position:absolute}
.btn{position:absolute;display:flex;align-items:center;justify-content:center;gap:10px;border-radius:40px;color:#fff;font-weight:700;background:linear-gradient(90deg,var(--btn-a),var(--btn-b));box-shadow:0 6px 14px rgba(120,20,16,.25)}
.btn .arrow{width:20px;height:20px}
/* header */
.topline{left:0;top:0;width:1200px;height:3px;background:var(--red)}
.header{left:0;top:3px;width:1200px;height:90px;background:#fff;z-index:3}
.brand-ribbon{left:110px;top:0;width:171px;height:176px;background:linear-gradient(180deg,#a8151a,#7e0f10);clip-path:polygon(0 0,100% 0,100% 88%,50% 100%,0 88%);z-index:5;display:flex;flex-direction:column;align-items:center;justify-content:center;padding-bottom:20px}
.brand-mark{width:14px;height:14px;border-radius:50%;background:#fff;margin-bottom:12px}
.brand-name{color:#fff;font-weight:900;font-size:16px;line-height:1.15;text-align:center;letter-spacing:.5px}
.nav{top:33px;font-size:17px;font-weight:400;color:#222}
.nav.active{color:var(--red);font-weight:700}
.icon-btn{top:23px;width:42px;height:42px;border-radius:50%;background:linear-gradient(180deg,#a51a17,#6e100e);display:flex;align-items:center;justify-content:center}
/* hero */
.hero{left:0;top:93px;width:1200px;height:655px}
.hero-kicker{top:75px;right:77px;color:var(--red);font-weight:900;font-size:34px;letter-spacing:.5px}
.hero-title{top:122px;right:77px;color:#fff;font-weight:900;font-size:66px;line-height:73px;text-align:right;letter-spacing:-.5px;text-shadow:0 2px 8px rgba(0,0,0,.35)}
.hero-lead{top:318px;right:77px;width:480px;color:#fff;font-weight:700;font-size:20px;line-height:33px;text-align:right}
/* intro */
.section-title{left:0;width:1200px;text-align:center;font-weight:900;font-size:46px;line-height:63px;text-transform:uppercase;letter-spacing:-.3px}
.section-copy{left:160px;width:880px;text-align:center;color:var(--muted);font-size:16.5px;line-height:31.6px}
/* gallery */
.tile{position:absolute;border-radius:20px;overflow:hidden}
/* about */
.about-photo{left:0;top:1832px;width:634px;height:552px;border-radius:0 22px 22px 0;background:linear-gradient(135deg,#8a9a8c 0%,#b9a98a 40%,#c9a45a 60%,#3c3a35 100%)}
.about-card{left:526px;top:1896px;width:561px;height:424px;background:#fff;border-radius:30px;box-shadow:0 10px 40px rgba(0,0,0,.08)}
/* services */
.svc{position:absolute;top:2581px;width:317px;height:457px;background:#fff;border-radius:20px;box-shadow:0 8px 30px rgba(0,0,0,.08)}
.svc-photo{position:absolute;left:9px;top:11px;width:299px;height:225px;border-radius:20px}
.svc-title{position:absolute;top:256px;left:0;width:100%;text-align:center;font-weight:900;font-size:21px}
.svc-copy{position:absolute;top:292px;left:20px;width:277px;text-align:center;color:var(--muted);font-size:14.5px;line-height:26.5px}
.svc .btn{left:88px;top:383px;width:143px;height:42px;font-size:15px}
.svc .btn .arrow{width:15px;height:15px}
/* footer */
.footer{left:0;top:3130px;width:1200px;height:407px}
.foot-brand{left:110px;top:3330px;width:190px;text-align:center;color:#fff;font-weight:900;font-size:21px;line-height:1.2}
.foot-brand .dot{width:16px;height:16px;border-radius:50%;background:#fff;margin:0 auto 12px}
.foot-head{top:3236px;color:#fff;font-weight:900;font-size:22px;letter-spacing:-.3px}
.foot-list{top:3276px;list-style:none;color:#fff;font-size:15px}
.foot-list li{height:33.5px;display:flex;align-items:flex-start;gap:16px}
.foot-list .chev{font-size:15px;width:14px}
.contact-list li{gap:18px}
.contact-list svg{flex:none;margin-top:2px}
.divider{left:110px;top:3467px;width:978px;height:1px;background:rgba(255,255,255,.2)}
.copyright{left:110px;top:3487px;color:#fff;font-size:13px}
.social{top:3482px;width:28px;height:28px;border-radius:50%;background:var(--red)}
</style>
</head>
<body>

<!-- header -->
<div class="abs topline"></div>
<div class="abs header"></div>
<div class="abs brand-ribbon">
  <div class="brand-mark"></div>
  <div class="brand-name">EMBER PLANK<br>CATERING</div>
</div>
<nav>
  <span class="abs nav active" style="left:368px;z-index:4">Home</span>
  <span class="abs nav" style="left:466px;z-index:4">About Us</span>
  <span class="abs nav" style="left:587px;z-index:4">Our Menu</span>
  <span class="abs nav" style="left:715px;z-index:4">Reviews</span>
  <span class="abs nav" style="left:829px;z-index:4">Contact Us</span>
</nav>
<div class="abs icon-btn" style="left:948px;z-index:4"><svg width="14" height="14" viewBox="0 0 14 14"><circle cx="6" cy="6" r="4" fill="none" stroke="#fff" stroke-width="2"/><path d="M9 9l4 4" stroke="#fff" stroke-width="2"/></svg></div>
<div class="abs icon-btn" style="left:997px;z-index:4"><svg width="15" height="14" viewBox="0 0 15 14"><path d="M7.5 13 1.8 7.3a3.2 3.2 0 0 1 5.7-3.6 3.2 3.2 0 0 1 5.7 3.6z" fill="none" stroke="#fff" stroke-width="1.8"/></svg></div>
<div class="abs icon-btn" style="left:1047px;z-index:4"><svg width="15" height="14" viewBox="0 0 15 14"><path d="M0 1h3l2 8h8l1.5-6H4" fill="none" stroke="#fff" stroke-width="1.8"/><circle cx="6" cy="12" r="1.3" fill="#fff"/><circle cx="12" cy="12" r="1.3" fill="#fff"/></svg></div>

<!-- hero -->
<section class="abs hero">
  <svg class="abs" style="left:0;top:0" width="1200" height="655" viewBox="0 0 1200 655" role="img" aria-label="Smiling chef grilling sausages on an outdoor barbecue">
    <defs>
      <linearGradient id="heroFill" x1="0" y1="0" x2="1" y2="1">
        <stop offset="0" stop-color="#4d5a3a"/>
        <stop offset=".35" stop-color="#6b5440"/>
        <stop offset=".6" stop-color="#3e4a2e"/>
        <stop offset="1" stop-color="#1f2418"/>
      </linearGradient>
      <linearGradient id="heroShade" x1="0" y1="0" x2="1" y2="0">
        <stop offset="0" stop-color="#000" stop-opacity="0"/>
        <stop offset="1" stop-color="#000" stop-opacity=".35"/>
      </linearGradient>
    </defs>
    <path d="M110 532 Q597 778 1085 532 L1085 500 L110 500 Z" fill="#c8161d"/>
    <path d="M0 0 H1200 V484 Q600 758 0 484 Z" fill="url(#heroFill)"/>
    <path d="M0 0 H1200 V484 Q600 758 0 484 Z" fill="url(#heroShade)"/>
  </svg>
  <div class="abs hero-kicker">CALIFORNIA</div>
  <div class="abs hero-title">EMBER PLANK<br>CATERING</div>
  <p class="abs hero-lead">Lorem ipsum dolor sit amet, consectetur adipiscing elit, sed do eiusmod tempor incididunt ut</p>
  <a class="btn" style="left:928px;top:401px;width:195px;height:55px;font-size:19px">Get Started
    <svg class="arrow" viewBox="0 0 20 20"><circle cx="10" cy="10" r="9" fill="#fff"/><path d="M6 10h7M10 6.5 13.5 10 10 13.5" fill="none" stroke="#8a1512" stroke-width="2.2"/></svg></a>
</section>

<!-- intro -->
<h2 class="abs section-title" style="top:816px">Chef-Made Food<br>Exactly When You Want It</h2>
<p class="abs section-copy" style="top:955px">Sed ut perspiciatis unde omnis iste natus error sit voluptatem accusantium doloremque laudantium, totam aperiam, eaque ipsa quae ab illo inventore veritatis et quasi architecto beatae vitae dicta sunt explicabo. Nemo enim ipsam voluptatem quia voluptas sit aspernatur aut odit aut fugit, sed quia consequuntur magni dolores</p>
<a class="btn" style="left:503px;top:1075px;width:194px;height:55px;font-size:19px">Read More
  <svg class="arrow" viewBox="0 0 20 20"><circle cx="10" cy="10" r="9" fill="#fff"/><path d="M6 10h7M10 6.5 13.5 10 10 13.5" fill="none" stroke="#8a1512" stroke-width="2.2"/></svg></a>

<!-- gallery -->
<div class="tile" style="left:-40px;top:1240px;width:198px;height:431px;background:linear-gradient(160deg,#5a6b3a,#6a3a22 45%,#2a2220)" role="img" aria-label="Sausages and vegetable skewers on a grill"></div>
<div class="tile" style="left:185px;top:1192px;width:258px;height:208px;background:linear-gradient(150deg,#7d8a6a,#c9b99a 40%,#3a3430)" role="img" aria-label="Man in sunglasses grilling corn and meat"></div>
<div class="tile" style="left:185px;top:1424px;width:258px;height:294px;background:linear-gradient(140deg,#8a3a20,#c0552e 45%,#2a2220)" role="img" aria-label="Close-up of grilled sausages on grates"></div>
<div class="tile" style="left:471px;top:1192px;width:258px;height:526px;background:linear-gradient(180deg,#e6d8d0 0%,#d6b0a6 40%,#d46060 75%,#c8161d 100%);box-shadow:0 14px 30px rgba(0,0,0,.15)" role="img" aria-label="Two men grilling outdoors at sunset"></div>
<div class="tile" style="left:757px;top:1192px;width:256px;height:208px;background:linear-gradient(150deg,#3a3230,#8a3a20 50%,#5a4a40)" role="img" aria-label="Smoking grill with sausages and meat"></div>
<div class="tile" style="left:757px;top:1424px;width:256px;height:294px;background:linear-gradient(140deg,#5a7a3a,#c8a040 50%,#2a2a28)" role="img" aria-label="Friends laughing around a barbecue"></div>
<div class="tile" style="left:1042px;top:1240px;width:200px;height:431px;background:linear-gradient(160deg,#e8e8e4,#b99a80 45%,#c2541e 70%,#2a2a28)" role="img" aria-label="Man in apron cooking at a grill"></div>

<!-- about -->
<div class="abs about-photo" role="img" aria-label="Smiling man in straw hat grilling in a garden with guests"></div>
<div class="abs about-card">
  <h2 class="abs" style="left:0;top:50px;width:561px;text-align:center;font-weight:900;font-size:44px">ABOUT US</h2>
  <p class="abs" style="left:50px;top:123px;width:461px;text-align:center;color:var(--muted);font-size:16.5px;line-height:31.6px">Sed ut perspiciatis unde omnis iste natus error sit voluptatem accusantium doloremque laudantium, totam aperiam, eaque ipsa quae ab illo inventore veritatis et quasi architecto beatae vitae dicta sunt explicabo. Nemo enim ipsam voluptatem quia voluptas sit aspernatur aut odit aut fugit</p>
  <a class="btn" style="left:182px;top:305px;width:195px;height:55px;font-size:19px">Read More
    <svg class="arrow" viewBox="0 0 20 20"><circle cx="10" cy="10" r="9" fill="#fff"/><path d="M6 10h7M10 6.5 13.5 10 10 13.5" fill="none" stroke="#8a1512" stroke-width="2.2"/></svg></a>
</div>

<!-- services -->
<h2 class="abs section-title" style="top:2463px">We’ve Got You Covered</h2>
<p class="abs" style="left:0;top:2530px;width:1200px;text-align:center;color:var(--muted);font-size:18.5px">Sed ut perspiciatis unde omnis iste natus error sit voluptatem accusantium doloremque laudantium</p>

<div class="svc" style="left:111px">
  <div class="svc-photo" style="background:linear-gradient(140deg,#c9a06a,#6a7a50 45%,#3a2a22)" role="img" aria-label="Guests gathered around a grill at a catered event"></div>
  <div class="svc-title">CATERED EVENTS</div>
  <p class="svc-copy">Lorem ipsum dolor sit amet, consectetur adipiscing elit, sed do eiusmod tempor incididunt ut labore et dolore magn</p>
  <a class="btn">Read More <svg class="arrow" viewBox="0 0 20 20"><circle cx="10" cy="10" r="9" fill="#fff"/><path d="M6 10h7M10 6.5 13.5 10 10 13.5" fill="none" stroke="#8a1512" stroke-width="2.2"/></svg></a>
</div>
<div class="svc" style="left:454px">
  <div class="svc-photo" style="background:linear-gradient(150deg,#4a4a44,#6a8a4a 45%,#c8b08a 70%,#7a3a30)" role="img" aria-label="Chef grilling at an outdoor workplace lunch"></div>
  <div class="svc-title">WORKPLACE DINING</div>
  <p class="svc-copy">Lorem ipsum dolor sit amet, consectetur adipiscing elit, sed do eiusmod tempor incididunt ut labore et dolore magn</p>
  <a class="btn">Read More <svg class="arrow" viewBox="0 0 20 20"><circle cx="10" cy="10" r="9" fill="#fff"/><path d="M6 10h7M10 6.5 13.5 10 10 13.5" fill="none" stroke="#8a1512" stroke-width="2.2"/></svg></a>
</div>
<div class="svc" style="left:796px">
  <div class="svc-photo" style="background:linear-gradient(140deg,#8a8a80,#c8a040 45%,#5a6a8a 70%,#2a2a28)" role="img" aria-label="Plate of grilled food being handed to a guest"></div>
  <div class="svc-title">DELIVERY</div>
  <p class="svc-copy">Lorem ipsum dolor sit amet, consectetur adipiscing elit, sed do eiusmod tempor incididunt ut labore et dolore magn</p>
  <a class="btn">Read More <svg class="arrow" viewBox="0 0 20 20"><circle cx="10" cy="10" r="9" fill="#fff"/><path d="M6 10h7M10 6.5 13.5 10 10 13.5" fill="none" stroke="#8a1512" stroke-width="2.2"/></svg></a>
</div>

<!-- footer -->
<svg class="abs footer" viewBox="0 0 1200 407">
  <path d="M0 75 Q260 12 540 0 Q260 30 0 126 Z" fill="#c8161d"/>
  <path d="M1200 75 Q940 12 660 0 Q940 30 1200 126 Z" fill="#c8161d"/>
  <path d="M0 134 Q300 20 600 0 Q900 20 1200 134 V407 H0 Z" fill="#560e0b"/>
</svg>

<div class="abs foot-brand"><div class="dot"></div>EMBER PLANK<br>CATERING</div>

<div class="abs foot-head" style="left:401px">QUICK LINKS</div>
<ul class="abs foot-list" style="left:401px">
  <li><span class="chev">»</span>Home</li>
  <li><span class="chev">»</span>About Us</li>
  <li><span class="chev">»</span>Our Menu</li>
  <li><span class="chev">»</span>Reviews</li>
  <li><span class="chev">»</span>Contact Us</li>
</ul>

<div class="abs foot-head" style="left:627px">HELP LINKS</div>
<ul class="abs foot-list" style="left:627px">
  <li><span class="chev">»</span>Help</li>
  <li><span class="chev">»</span>Support</li>
  <li><span class="chev">»</span>Privacy Policy</li>
  <li><span class="chev">»</span>Terms Of Use</li>
</ul>

<div class="abs foot-head" style="left:837px">CONTACT US</div>
<ul class="abs foot-list contact-list" style="left:837px;width:260px">
  <li style="height:67px;line-height:33px;margin-top:-8px"><svg width="12" height="15" viewBox="0 0 12 15" style="margin-top:10px"><path d="M6 14S1 8.5 1 5.5a5 5 0 0 1 10 0C11 8.5 6 14 6 14z" fill="#fff"/><circle cx="6" cy="5.5" r="1.8" fill="#560e0b"/></svg><span>Ember Plank Catering, Oakvale, California</span></li>
  <li><svg width="14" height="14" viewBox="0 0 14 14"><path d="M3 1l2.5 3-1.5 1.5a8 8 0 0 0 4.5 4.5L10 8.5l3 2.5-1.5 2C6 13 1 8 1 2.5z" fill="#fff"/></svg>+1 555 014 2270</li>
  <li><svg width="15" height="12" viewBox="0 0 15 12"><rect x="0" y="1" width="15" height="10" rx="1" fill="#fff"/><path d="M0.5 1.5 7.5 7l7-5.5" fill="none" stroke="#560e0b" stroke-width="1.3"/></svg>hello@emberplank.com</li>
</ul>

<div class="abs divider"></div>
<div class="abs copyright">(C) Copyright 2024 | All Rights Reserved</div>
<div class="abs social" style="left:988px"></div>
<div class="abs social" style="left:1024px"></div>
<div class="abs social" style="left:1060px"></div>

</body>
</html>
```